Cat-products company needs smart, yet endearing, business card

We need a business card design for a new, but up-and-running, business based in Honolulu, Hawaii. The business is Purrnest Nook Co. Our first product is the most environmentally-friendly cat grass kit ever seen on the planet. Future products, currently in the R&D phase, will include a variety of exciting cat scratchers. We also do consulting work to help apartment-dwellers make their home more cat-friendly and, in the future, plan on doing full, custom installs of structure to create high walkways for cats.

Target Market(s)

Middle-aged, apartment-dwelling, middle-class workers who own 1 or more cats and who dote on them.

Industry/Entity Type

Pet Care

Contact Information for Business Card

A striking, professional, yet warm and friendly design is what we're after.

Font styles to use
Serif
Sans Serif
Other font styles liked:
• Comfortaa

Colors

Designer to choose colors to be used in the design.

Requirements
Must have
• The company logo: (see attachment)
• The company name: Purrnest Nook Co
• The web address: www.purrnestnookco.com
• Email: support@purrnestnookco.com
• Phone: +1 (808) 571 6023
• Update (Fri Jun 30 3017 7:45pm Hawaii Time) I would like, is possible, uploaded picture of the cat grass kit on the back of the card with some text along the lines of: Purrnest Nook Co - Maker Of The Leafiest Feline Sprout Set Yet
Nice to have
• A cat picture, cartoon, real or silhouette that illustrates cats in action and/or relaxing; ie using the apartment space to live, play and relax in and being well-contented.
• Most of the website is done in the font: Comfortaa. It might be nice to continue using this for brand consistency.
Should not have
• Hard-to-read fonts.

```html
<!DOCTYPE html>
<html lang="en">
<head>
<meta charset="utf-8">
<title>Purrnest Nook Co – Business Cards</title>
<link rel="stylesheet" href="https://fonts.googleapis.com/css2?family=Comfortaa:wght@400;700&family=Nunito:wght@400;600&display=swap">
<style>
  :root {
    --brown: #55332d;
    --yellow: #fcb316;
    --white: #ffffff;
    --stage: #3e3e3e;
    --ink: #3a2420;
  }
  * { margin: 0; padding: 0; box-sizing: border-box; }
  html, body { width: 1189px; height: 1200px; overflow: hidden; }
  body { background: var(--stage); font-family: "Comfortaa", sans-serif; }
  .canvas { position: relative; width: 1189px; height: 1200px; }

  .card { position: absolute; overflow: hidden; border-radius: 33px; }

  .brand-mark { position: absolute; left: 50%; transform: translateX(-50%); background: var(--brown); }
  .brand-name {
    position: absolute; left: 0; right: 0; text-align: center;
    font-family: "Comfortaa", sans-serif; font-weight: 700; line-height: 1.05;
  }

  /* front card */
  .card--front { left: 42px; top: 233px; width: 437px; height: 764px; background: var(--white); }
  .card--front .brand-mark { top: 62px; width: 132px; height: 132px; border-radius: 8px; }
  .card--front .brand-name { top: 212px; font-size: 46px; color: var(--yellow); }

  .person { position: absolute; left: 0; right: 0; top: 370px; text-align: center; line-height: 1.15; }
  .person__name { font-size: 29px; font-weight: 700; color: var(--brown); }
  .person__name .first { color: var(--yellow); }
  .person__role { font-size: 20px; color: var(--brown); margin-top: 4px; }

  .contact { position: absolute; left: 0; right: 0; text-align: center; line-height: 1.2; }
  .contact__label { font-family: "Nunito", sans-serif; font-weight: 600; font-size: 17px; color: var(--yellow); }
  .contact__value { font-family: "Nunito", sans-serif; font-size: 22px; color: var(--ink); margin-top: 5px; }
  .contact--phone { top: 478px; }
  .contact--email { top: 563px; }
  .contact--email .contact__value { font-family: "Comfortaa", sans-serif; font-size: 19px; }
  .divider { position: absolute; left: 66px; right: 66px; top: 549px; height: 1px; background: var(--yellow); }

  .stripe { position: absolute; left: 0; right: 0; top: 701px; height: 7px; background: var(--yellow); }
  .footer-band {
    position: absolute; left: 0; right: 0; bottom: 0; height: 56px; background: var(--brown);
    display: flex; align-items: center; justify-content: center;
    color: var(--yellow); font-size: 19px; font-weight: 700; letter-spacing: 0.5px;
  }

  /* back card, logo side */
  .card--back { left: 504px; top: 230px; width: 643px; height: 367px; background: var(--brown); }
  .card--back .brand-mark { top: 84px; width: 92px; height: 92px; border-radius: 6px; background: var(--yellow); }
  .card--back .brand-name { top: 198px; font-size: 40px; color: var(--white); }
  .card--back .site { position: absolute; left: 0; right: 0; top: 301px; text-align: center; color: var(--white); font-size: 17px; font-weight: 700; }

  /* back card, photo side */
  .card--scene { left: 504px; top: 627px; width: 643px; height: 369px; background: var(--white); }
  .scene-photo {
    position: absolute; left: 0; top: 0; width: 377px; height: 328px;
    background: linear-gradient(100deg, #eceae6 0%, #f6f5f2 35%, #d9c9a6 55%, #c98a4a 72%, #f3f1ee 100%);
  }
  .scene-brand { position: absolute; left: 397px; width: 226px; top: 0; height: 328px; }
  .card--scene .brand-mark { top: 36px; width: 96px; height: 96px; border-radius: 6px; }
  .card--scene .brand-name { top: 150px; font-size: 33px; color: var(--yellow); }
  .social { position: absolute; left: 0; right: 0; top: 264px; display: flex; justify-content: center; gap: 16px; }
  .social__item { width: 27px; height: 27px; background: var(--brown); border-radius: 2px; }
  .card--scene .footer-band { height: 41px; font-size: 17px; letter-spacing: 2px; }
</style>
</head>
<body>
<main class="canvas">

  <section class="card card--front">
    <div class="brand-mark"></div>
    <div class="brand-name">Purrnest<br>Nook Co</div>
    <div class="person">
      <div class="person__name"><span class="first">Employee</span> Name</div>
      <div class="person__role">Manager</div>
    </div>
    <div class="contact contact--phone">
      <div class="contact__label">Phone</div>
      <div class="contact__value">+1 (808) 571 6023</div>
    </div>
    <div class="divider"></div>
    <div class="contact contact--email">
      <div class="contact__label">Email</div>
      <div class="contact__value">support@purrnestnookco.com</div>
    </div>
    <div class="stripe"></div>
    <div class="footer-band">www.purrnestnookco.com</div>
  </section>

  <section class="card card--back">
    <div class="brand-mark"></div>
    <div class="brand-name">Purrnest<br>Nook Co</div>
    <div class="site">www.purrnestnookco.com</div>
  </section>

  <section class="card card--scene">
    <div class="scene-photo" role="img" aria-label="Photo of cats relaxing on a wall-mounted cat tree and a ginger cat stretching up a sisal scratching post"></div>
    <div class="scene-brand">
      <div class="brand-mark"></div>
      <div class="brand-name">Purrnest<br>Nook Co</div>
      <div class="social">
        <span class="social__item"></span>
        <span class="social__item"></span>
        <span class="social__item"></span>
        <span class="social__item"></span>
      </div>
    </div>
    <div class="footer-band">www.purrnestnookco.com</div>
  </section>

</main>
</body>
</html>
```